Investor Slide Deck

Simple idea - take a model investor deck and build out a investor deck for K7V. I will complete the data, I need a template to work from within. I will attach a model investor deck and a blank K7V that I need built out to K7V. Use the K7V Pwrpt to build out the investor deck

```html
<!DOCTYPE html>
<html lang="en">
<head>
<meta charset="utf-8">
<title>K7V Investor Deck 2024</title>
<link href="https://fonts.googleapis.com/css2?family=Montserrat:wght@400;500;600&family=Roboto:wght@400;500;700&display=swap" rel="stylesheet">
<style>
:root{
  --stage:#6f6f6f;
  --deep:#1f4d5b;
  --tab:#216f88;
  --teal:#17b0a8;
  --orange:#fb5a0c;
  --yellow:#f3b11e;
  --blue:#1d6a85;
  --ink:#222b31;
  --bar:#13809f;
  --ebitda:#fb8c13;
}
*{margin:0;padding:0;box-sizing:border-box}
html,body{width:1076px;height:1200px;overflow:hidden;background:var(--stage)}
body{position:relative;font-family:Roboto,Arial,sans-serif}
.slide{position:absolute;width:788px;height:443px;transform-origin:0 0;transform:scale(.5912);overflow:hidden}
.slide.light{background:linear-gradient(180deg,#ffffff 0%,#f6f7f8 60%,#eceeef 100%)}
.slide.dark{background:linear-gradient(135deg,#1e4a59 0%,#245a69 100%);color:#fff}
.abs{position:absolute}
.tab{position:absolute;left:0;top:0;height:58px;background:var(--tab);border-radius:0 29px 29px 0;color:#fff;font:500 23px/58px Montserrat,sans-serif;letter-spacing:1.2px;white-space:nowrap}
.tab .dot{position:absolute;top:23px;width:12px;height:12px;border-radius:50%;background:#fff}
.brand{position:absolute;right:19px;display:flex;align-items:center;gap:7px;white-space:nowrap}
.brand .mark{font:600 30px/1 Montserrat,sans-serif;color:var(--orange)}
.brand .name{font:500 13px/1 Montserrat,sans-serif;color:var(--ink);letter-spacing:.2px}
.footer{position:absolute;left:0;bottom:0;width:788px;height:24px}
.footer-text{position:absolute;left:0;width:788px;bottom:3px;text-align:center;font:500 9px Roboto,sans-serif;color:#fff}
.page{position:absolute;left:754px;top:410px;width:24px;height:24px;border-radius:50%;background:var(--teal);border:2px solid #fff;color:#fff;font:700 10px/20px Roboto,sans-serif;text-align:center}
.photo{position:absolute}
.prob-title{position:absolute;font:700 12.5px Roboto,sans-serif;color:#333;white-space:nowrap}
.prob-body{position:absolute;font:400 8.5px/11px Roboto,sans-serif;color:#555}
.r{text-align:right}
.bubble{position:absolute;width:182px;height:182px;border-radius:50%;color:#fff;text-align:center;padding:20px 30px 0}
.bubble h3{font:700 12.5px/14px Roboto,sans-serif;margin:6px 0 5px}
.bubble p{font:400 8px/10.6px Roboto,sans-serif}
.bubble svg{display:block;margin:0 auto}
.card{position:absolute;width:228px;color:#fff;overflow:hidden}
.card .pic{height:155px;border-bottom:3px solid #fff;border-radius:0 0 50% 50%/0 0 34px 34px}
.card h3{font:700 17px/18px Roboto,sans-serif;margin:22px 0 10px 32px}
.card ul{list-style:none;margin-left:32px;font:400 9.5px/19px Roboto,sans-serif}
.card ul.tight{line-height:14.5px}
.market-box{position:absolute;border:4px solid var(--teal);background:#fff}
.market-text{position:absolute;font:400 14px/20.5px Roboto,sans-serif;color:#222}
.market-text b{color:var(--tab);font-weight:500}
.contact-row{position:absolute;left:127px;display:flex;align-items:center;gap:14px;font:700 14px/18px Roboto,sans-serif;color:#fff;white-space:nowrap}
.ico{width:30px;height:30px;border-radius:50%;display:flex;align-items:center;justify-content:center;flex:none}
</style>
</head>
<body>

<section class="slide dark" style="left:66.2px;top:60.3px;background:#1f5766">
  <div class="photo" role="img" aria-label="Engineer in a field inspecting long rows of solar panels" style="left:340px;top:0;width:448px;height:443px;background:linear-gradient(90deg,rgba(31,87,102,0) 0%,rgba(102,150,160,.75) 35%,#8fb1b8 70%,#6f9aa4 100%)"></div>
  <svg class="abs" style="left:0;top:0" width="788" height="443"><path d="M38,226 A180,180 0 0,0 398,226" fill="none" stroke="var(--teal)" stroke-width="6"/></svg>
  <div class="abs" style="left:0;width:436px;top:128px;text-align:center;font:600 72px/1 Montserrat,sans-serif;color:var(--orange)">K7V</div>
  <div class="abs" style="left:0;width:436px;top:218px;text-align:center;font:500 20px/1 Montserrat,sans-serif;color:#fff;letter-spacing:.5px;white-space:nowrap">KESTREL SEVEN VENTURES</div>
  <div class="abs" style="left:100px;top:282px;font:400 26px/1 Montserrat,sans-serif;color:#fff;letter-spacing:1.2px;white-space:nowrap">Investor Deck, 2024</div>
</section>

<section class="slide dark" style="left:543.9px;top:60.3px">
  <div class="tab" style="top:21px;width:320px;padding-left:22px">BUSINESS MODEL<span class="dot" style="left:290px"></span></div>
  <div class="abs" style="right:12px;top:18px;text-align:center;white-space:nowrap">
    <div style="font:600 40px/1 Montserrat,sans-serif;color:var(--orange)">K7V</div>
    <div style="font:500 11px/1 Montserrat,sans-serif;color:#fff;margin-top:14px">KESTREL SEVEN VENTURES</div>
  </div>
  <div class="photo" role="img" aria-label="Single monocrystalline solar panel" style="left:144px;top:108px;width:174px;height:174px;border-radius:50%;background:radial-gradient(circle,#2a2f36 0 22%,#8ed6ef 23%);border:3px solid #a7e2f4"></div>
  <div class="photo" role="img" aria-label="Aerial view of a large solar farm" style="left:449px;top:108px;width:174px;height:174px;border-radius:50%;background:linear-gradient(160deg,#8fae6d 0%,#5f86b0 40%,#37608e 100%);border-bottom:4px solid var(--teal)"></div>
  <div class="abs" style="left:131px;width:200px;top:298px;text-align:center;font:500 14px/1 Montserrat,sans-serif;letter-spacing:1px;white-space:nowrap">SALES OF SOLAR PANEL</div>
  <div class="abs" style="left:126px;width:210px;top:325px;text-align:center;font:400 9.5px/13.6px Roboto,sans-serif">Solar Panels manufactured at our manufacturing facility will be sold via different channels that we will develop. We aim to reach out to B2C customers via a separate franchise model that we will begin after commencement of manufacturing operations.</div>
  <div class="abs" style="left:396px;width:280px;top:298px;text-align:center;font:500 14px/15px Montserrat,sans-serif;letter-spacing:1px">GOVERNMENT AND INDUSTRIAL<br>EPC PROJECTS</div>
  <div class="abs" style="left:431px;width:210px;top:337px;text-align:center;font:400 9.5px/13.6px Roboto,sans-serif">We project about half of our manufactured solar panels to be used in EPC projects that we will bid for. We aim to generate gross margins of 10% - 12% on the overall projects.</div>
  <svg class="footer" viewBox="0 0 788 24" preserveAspectRatio="none"><path d="M0,24 L0,14 Q394,2 788,10 L788,24 Z" fill="var(--teal)"/></svg>
  <div class="footer-text">Private &amp; Confidential | 2024</div>
  <div class="page">05</div>
</section>

<section class="slide light" style="left:66.2px;top:332.8px">
  <div class="tab" style="width:271px;padding-left:60px">PROBLEMS<span class="dot" style="left:241px"></span></div>
  <div class="brand" style="top:26px"><span class="mark">K7V</span><span class="name">KESTREL SEVEN VENTURES</span></div>
  <p class="abs" style="left:34px;top:78px;font:400 16.5px/23px Roboto,sans-serif;color:#333">Every year, the rise in prices of electricity is burning a hole in the pocket of consumers.<br>Solar Power is a reliable solution, but the industry is facing its own set of challenges.</p>
  <svg class="abs" style="left:246px;top:142px" width="240" height="220" viewBox="-120 -110 240 220">
    <path d="M0,0 L-55,-54 A77,77 0 0,1 2,-77 Z" fill="#f47a2a"/>
    <path d="M0,0 L2,-77 A77,77 0 0,1 70,-31 Z" fill="#7b5be0"/>
    <path d="M0,0 L70,-31 A77,77 0 0,1 55,54 Z" fill="#2fb2d6"/>
    <path d="M0,0 L55,54 A77,77 0 0,1 -38,67 Z" fill="#3fd5b0"/>
    <path d="M0,0 L-38,67 A77,77 0 0,1 -55,-54 Z" fill="#f154a9"/>
    <g fill="#fff" stroke="#555" stroke-width="1.5">
      <circle cx="-42" cy="-60" r="30"/><circle cx="42" cy="-60" r="30"/>
      <circle cx="68" cy="18" r="30"/><circle cx="0" cy="69" r="30"/><circle cx="-68" cy="18" r="30"/>
    </g>
    <path d="M-42,-74 L-29,-50 L-55,-50 Z" fill="#f08a1c"/><rect x="-43" y="-68" width="2" height="10" fill="#fff"/><rect x="-43" y="-56" width="2" height="2" fill="#fff"/>
    <path d="M32,-50 L48,-66" stroke="#7b5be0" stroke-width="5" stroke-linecap="round"/><circle cx="50" cy="-68" r="6" fill="none" stroke="#7b5be0" stroke-width="3"/>
    <g fill="#2fb2d6"><circle cx="68" cy="11" r="5"/><circle cx="58" cy="14" r="4"/><circle cx="78" cy="14" r="4"/><path d="M60,26 Q68,14 76,26 Z"/><path d="M51,25 Q58,17 63,24 Z"/><path d="M73,24 Q78,17 85,25 Z"/></g>
    <g fill="none" stroke="#3fd5b0" stroke-width="4"><circle cx="-5" cy="72" r="6"/><circle cx="9" cy="64" r="3.5"/></g>
    <path d="M-75,6 L-64,6 L-60,10 L-60,30 L-75,30 Z" fill="#f154a9"/>
  </svg>
  <div class="prob-title r" style="right:508px;top:154px">Poor Quality Components</div>
  <div class="prob-body r" style="right:508px;top:173px;width:220px">The use of low-quality solar panels and components in solar plant construction is impacting their efficiency and lifespan.</div>
  <div class="prob-title" style="left:448px;top:154px">Poor Installation</div>
  <div class="prob-body" style="left:448px;top:173px;width:200px">Solar plant installations demand precision; poor installation can lead to downtime, damage, and efficiency loss.</div>
  <div class="prob-title r" style="right:533px;top:241px">Lack of Awareness</div>
  <div class="prob-body r" style="right:533px;top:260px;width:215px">Limited awareness of government subsidies and inadequate financing options for high-cost solar plant purchases can lead to missed product benefits</div>
  <div class="prob-title" style="left:477px;top:241px">Unreliable Customer and Warranty Support</div>
  <div class="prob-body" style="left:477px;top:260px;width:270px">Challenges in reaching timely support and clarifying warranty terms can result in customer frustration and self-reliance for issue resolution.</div>
  <div class="prob-title" style="left:181px;width:360px;top:356px;text-align:center">Lack of Transparency in Pricing and Performance</div>
  <div class="prob-body" style="left:251px;width:220px;top:375px;text-align:center">Customers might encounter unexpected hidden costs during installation and lower energy generation than initially agreed upon.</div>
  <svg class="footer" viewBox="0 0 788 24" preserveAspectRatio="none"><path d="M0,24 L0,14 Q394,2 788,10 L788,24 Z" fill="var(--teal)"/></svg>
  <div class="footer-text">Private &amp; Confidential | 2024</div>
  <div class="page">02</div>
</section>

<section class="slide light" style="left:543.9px;top:332.8px">
  <div class="tab" style="width:361px;padding-left:38px">TARGET MARKETS<span class="dot" style="left:331px"></span></div>
  <div class="brand" style="top:26px"><span class="mark">K7V</span><span class="name">KESTREL SEVEN VENTURES</span></div>
  <div class="market-box" style="left:61px;top:71px;width:330px;height:337px"></div>
  <div class="market-box" style="left:406px;top:71px;width:322px;height:337px"></div>
  <div class="photo" role="img" aria-label="Map of India with short- and medium-term target states highlighted" style="left:155px;top:85px;width:145px;height:157px;border-radius:40% 40% 50% 50%;background:linear-gradient(160deg,#d6d6d6 0%,#f2782a 30%,#1a9aa7 55%,#d9d9d9 85%)"></div>
  <div class="photo" role="img" aria-label="World map highlighting India, the Middle East and Africa" style="left:421px;top:82px;width:292px;height:155px;border-radius:8px;background:linear-gradient(120deg,#168ea2 0%,#2e9fb0 40%,#f2782a 52%,#168ea2 62%,#1a97aa 100%)"></div>
  <div class="market-text" style="left:97px;top:260px;width:270px"><b>• Short Term</b> – Location, Maharashtra, MP, Maharashtra<br><b>• Medium Term</b> – All Indian States with Solar Power Demand<br>• Setting up of Certification process for Export Markets</div>
  <div class="market-text" style="left:457px;top:272px;line-height:24.5px"><b>• Long Term</b> – India<br><b>• Export Markets</b><span style="font-weight:500">–Middle East and<br>&nbsp;African Continent</span></div>
  <svg class="footer" viewBox="0 0 788 24" preserveAspectRatio="none"><path d="M0,24 L0,14 Q394,2 788,10 L788,24 Z" fill="var(--teal)"/></svg>
  <div class="footer-text">Private &amp; Confidential | 2024</div>
  <div class="page">06</div>
</section>

<section class="slide light" style="left:66.2px;top:604.8px">
  <div class="tab" style="width:271px;padding-left:50px">SOLUTIONS<span class="dot" style="left:241px"></span></div>
  <div class="brand" style="top:26px"><span class="mark">K7V</span><span class="name">KESTREL SEVEN VENTURES</span></div>
  <div class="bubble" style="left:96px;top:72px;background:var(--orange)">
    <svg width="18" height="16"><path d="M2,8 L7,13 L16,2" fill="none" stroke="#fff" stroke-width="3"/></svg>
    <h3>Quality Components</h3>
    <p>With a portfolio of 2500+ solar power plants, we excel in selecting technically compatible, premium components to guarantee long-term results, planning an automated facility for high-quality solar panels.</p>
  </div>
  <div class="bubble" style="left:303px;top:72px;background:var(--blue)">
    <svg width="18" height="16"><path d="M1,5 L9,1 L17,5 Z M3,6h2v7h-2z M8,6h2v7h-2z M13,6h2v7h-2z M1,14h16v2h-16z" fill="#fff"/></svg>
    <h3>Awareness About<br>Subsidies And Financing</h3>
    <p>Company Name Energy educates residential consumers about Central Government subsidies and collaborates with banks and NBFCs to facilitate solar financing for various client segments.</p>
  </div>
  <div class="bubble" style="left:510px;top:72px;background:var(--yellow)">
    <svg width="18" height="18"><circle cx="9" cy="9" r="6" fill="#fff"/><circle cx="9" cy="9" r="8.5" fill="none" stroke="#fff" stroke-width="2" stroke-dasharray="3 2.5"/></svg>
    <h3>Dedicated Customer<br>And Warranty Support</h3>
    <p>Company Name Energy's dedicated team offers comprehensive after-sales support, facilitating swift warranty-covered service at local offices for our Panels and Inverters, eliminating brand-related delays.</p>
  </div>
  <div class="bubble" style="left:199px;top:236px;background:var(--teal)">
    <svg width="18" height="18"><circle cx="9" cy="9" r="6.5" fill="none" stroke="#fff" stroke-width="3" stroke-dasharray="3 2"/><circle cx="9" cy="9" r="2.5" fill="#fff"/></svg>
    <h3>Efficient Installation</h3>
    <p>Our proficient design and site engineers create solar plants to precise technicalspecs, ensuring low-maintenance installations with a flawless track record of zero system failures.</p>
  </div>
  <div class="bubble" style="left:407px;top:236px;background:#0a0a0a;padding-top:16px">
    <svg width="20" height="16"><rect x="1" y="2" width="18" height="13" rx="2" fill="#fff"/><rect x="1" y="5" width="18" height="2" fill="#0a0a0a"/></svg>
    <h3 style="margin:3px 0 3px">Transparent Pricing<br>&amp; Performance</h3>
    <p>We ensure transparent pricing and performance commitments in our projects. Our designs are created with the shadow analysis of solar panels for optimum result. We also provide the projected power generation and payback report of solar plant using software.</p>
  </div>
  <svg class="footer" viewBox="0 0 788 24" preserveAspectRatio="none"><path d="M0,24 L0,14 Q394,2 788,10 L788,24 Z" fill="var(--teal)"/></svg>
  <div class="footer-text">Private &amp; Confidential | 2024</div>
  <div class="page">03</div>
</section>

<section class="slide light" style="left:543.9px;top:604.8px">
  <div class="tab" style="width:386px;padding-left:26px">FINANCIAL OVERVIEW<span class="dot" style="left:358px"></span></div>
  <div class="brand" style="top:26px"><span class="mark">K7V</span><span class="name">KESTREL SEVEN VENTURES</span></div>
  <p class="abs" style="left:38px;top:118px;font:400 25px/30px Roboto,sans-serif;color:#222;white-space:nowrap">We plan to<br>double our capacity<br>in the 4th year<br>of Operations</p>
  <svg class="abs" style="left:265px;top:87px;background:#fff;box-shadow:0 2px 8px rgba(0,0,0,.15)" width="472" height="315" viewBox="1185 1110 472 315" font-family="Roboto,sans-serif">
    <text x="1205" y="1147" font-size="13" font-weight="700" fill="#222">in ₹Cr</text>
    <rect x="1468" y="1133" width="170" height="243" fill="none" stroke="#13809f" stroke-width="1"/>
    <g fill="var(--bar)">
      <rect x="1236" y="1352" width="17" height="20"/><rect x="1321" y="1275" width="17" height="97"/>
      <rect x="1407" y="1262" width="17" height="110"/><rect x="1492" y="1162" width="18" height="210"/>
      <rect x="1578" y="1158" width="18" height="214"/>
    </g>
    <g fill="var(--ebitda)">
      <rect x="1260" y="1370" width="18" height="2"/><rect x="1346" y="1361" width="18" height="11"/>
      <rect x="1432" y="1358" width="18" height="14"/><rect x="1518" y="1341" width="18" height="31"/>
      <rect x="1604" y="1338" width="17" height="34"/>
    </g>
    <g font-size="11" font-weight="700" fill="var(--bar)" text-anchor="middle">
      <text x="1240" y="1339">₹205</text><text x="1329" y="1260">₹972</text><text x="1416" y="1248">₹1,109</text>
      <text x="1505" y="1152">₹2,088</text><text x="1586" y="1149">₹2,130</text>
    </g>
    <g font-size="11" font-weight="700" fill="#e8751a" text-anchor="middle">
      <text x="1273" y="1339">₹14</text><text x="1365" y="1342">₹112.5</text><text x="1447" y="1336">₹141</text>
      <text x="1537" y="1328">₹315</text><text x="1618" y="1327">₹335</text>
    </g>
    <g font-size="8" fill="#777" text-anchor="middle">
      <text x="1256" y="1387">2024</text><text x="1342" y="1387">2025</text><text x="1428" y="1387">2026</text>
      <text x="1514" y="1387">2027</text><text x="1600" y="1387">2028</text>
    </g>
    <rect x="1385" y="1397" width="5" height="5" fill="var(--bar)"/><text x="1392" y="1402" font-size="8" fill="#777">Revenue</text>
    <rect x="1436" y="1397" width="5" height="5" fill="var(--ebitda)"/><text x="1443" y="1402" font-size="8" fill="#777">EBITDA</text>
  </svg>
  <svg class="footer" viewBox="0 0 788 24" preserveAspectRatio="none"><path d="M0,24 L0,14 Q394,2 788,10 L788,24 Z" fill="var(--teal)"/></svg>
  <div class="footer-text">Private &amp; Confidential | 2024</div>
  <div class="page">07</div>
</section>

<section class="slide light" style="left:66.2px;top:877.3px">
  <div class="tab" style="width:278px;padding-left:22px">OUR SERVICES<span class="dot" style="left:250px"></span></div>
  <div class="brand" style="top:26px"><span class="mark">K7V</span><span class="name">KESTREL SEVEN VENTURES</span></div>
  <div class="card" style="left:29px;top:100px;height:293px;background:var(--orange)">
    <div class="pic" role="img" aria-label="House roof fitted with solar panels" style="background:linear-gradient(160deg,#3a5d8f 0%,#8e5a46 50%,#c7c2bb 100%)"></div>
    <h3>Solar Power for Homes</h3>
    <ul><li>• Electricity Bill to go to Zero</li><li>• Low Maintenance Cost</li><li>• Assured Warranty upto 25 Years</li><li>• Government Subsidies</li></ul>
  </div>
  <div class="card" style="left:280px;top:81px;height:292px;background:var(--blue)">
    <div class="pic" role="img" aria-label="Aerial view of solar panels on a commercial building rooftop" style="background:linear-gradient(160deg,#c9d2da 0%,#4f79a8 45%,#dfe4e8 100%)"></div>
    <h3>Solar Power for Business</h3>
    <ul><li>• Clean Energy</li><li>• Tax Benefits</li><li>• Grid Tied Systems</li><li>• Finance Support</li></ul>
  </div>
  <div class="card" style="left:531px;top:100px;height:293px;background:#e9ad1c">
    <div class="pic" role="img" aria-label="Utility-scale solar power plant beside green fields" style="background:linear-gradient(170deg,#7d9c48 0%,#95a8b7 40%,#4d6f9a 100%)"></div>
    <h3 style="margin-top:14px">Utility Scale Solar<br>Power Plant</h3>
    <ul class="tight"><li>• Generate and Sell electricity to<br>&nbsp;the government and industrial plants</li><li>• Long term stable prices for generated<br>&nbsp;electricity from solar power plant</li></ul>
  </div>
  <svg class="footer" viewBox="0 0 788 24" preserveAspectRatio="none"><path d="M0,24 L0,14 Q394,2 788,10 L788,24 Z" fill="var(--teal)"/></svg>
  <div class="footer-text">Private &amp; Confidential | 2024</div>
  <div class="page">04</div>
</section>

<section class="slide" style="left:543.9px;top:877.3px;background:#2f4f58">
  <div class="photo" role="img" aria-label="Technicians installing solar panels on a rooftop" style="left:0;top:0;width:788px;height:443px;background:linear-gradient(110deg,#3b5d66 0%,#7d9aa2 45%,#b7c7cb 70%,#6f8d96 100%)"></div>
  <svg class="abs" style="left:0;top:0" width="788" height="443">
    <circle cx="217" cy="216" r="180" fill="var(--deep)"/>
    <path d="M397,216 A180,180 0 0,1 60,303" fill="none" stroke="var(--teal)" stroke-width="6"/>
  </svg>
  <div class="abs" style="left:37px;width:360px;top:58px;text-align:center;font:600 64px/1 Montserrat,sans-serif;color:var(--orange)">K7V</div>
  <div class="abs" style="left:37px;width:360px;top:140px;text-align:center;font:500 20px/1 Montserrat,sans-serif;color:#fff;white-space:nowrap">KESTREL SEVEN VENTURES</div>
  <div class="contact-row" style="top:182px">
    <span class="ico" style="background:var(--orange)"><svg width="14" height="16"><path d="M7,1 C3,1 1,4 1,6.5 C1,10 7,15 7,15 C7,15 13,10 13,6.5 C13,4 11,1 7,1 Z" fill="#fff"/><circle cx="7" cy="6.5" r="2.2" fill="var(--orange)"/></svg></span>
    <span>48 Harbor Lane, Suite 310<br>Lakewood, OR 97035</span>
  </div>
  <div class="contact-row" style="top:238px">
    <span class="ico" style="background:var(--teal)"><svg width="14" height="14"><path d="M3,1 L5.5,1 L6.5,4.5 L5,5.8 C5.8,7.6 6.6,8.4 8.2,9.2 L9.5,7.7 L13,8.7 L13,11 C13,12.5 11.5,13 10,12.6 C5.5,11.4 2.6,8.5 1.4,4 C1,2.5 1.6,1 3,1 Z" fill="#fff"/></svg></span>
    <span>P. 555.014.2290</span>
  </div>
  <div class="contact-row" style="top:277px">
    <span class="ico" style="background:var(--yellow)"><svg width="14" height="14"><circle cx="7" cy="7" r="6" fill="none" stroke="#fff" stroke-width="1.5"/><path d="M1,7h12 M7,1v12" stroke="#fff" stroke-width="1.2"/><ellipse cx="7" cy="7" rx="2.6" ry="6" fill="none" stroke="#fff" stroke-width="1.2"/></svg></span>
    <span>hello@k7v.example</span>
  </div>
</section>

</body>
</html>
```